Fresh, modern, fun business card for pediatric dental practice

Need a business card for fresh, modern, fun pediatric dental practice

Clean look that matches our website's font and colors

We prefer the look of curved corners on business cards

Target Market(s)

parents (mothers) of young children, professionals, mid-high class

Industry/Entity Type

Dental

Contact Information for Business Card

Maplebrook Pediatric Dentistry
482 Quarry Lane
Suite 517
Fernhollow, ST 00000
555.555.0193
www.maplebrookkidsdental.example

Mei-Ran Tsai, DMD
Corinne Walbeck, DMD
(we are working on our email address, but we would like that on the card as well)

Font styles to use
Sans Serif

Requirements
Must have
• All info; we would also like to make cards for individual staff members
• colors from our website and color palatte, attatched
• use same font and design as website for branding
Nice to have
• clean, simple card that has a pop of color
• we would like to see a few designs with our tag line "where smiles get brighter"
• we are not sure if we want to have it on there or not
• we would like to see a few designs incorporating the ribbon graphic on our website where the word WELCOME is

```html
<!DOCTYPE html>
<html lang="en">
<head>
<meta charset="utf-8">
<title>Maplebrook Pediatric Dentistry – Business Card</title>
<link rel="stylesheet" href="https://fonts.googleapis.com/css2?family=Lato:wght@400;700&family=Varela+Round&display=swap">
<style>
  :root {
    --magenta: #d0318f;
    --sun: #f3b11f;
    --ink: #555555;
    --paper: #ffffff;
    --backdrop: #d6d6d6;
  }
  * { box-sizing: border-box; margin: 0; padding: 0; }
  html, body { width: 1200px; height: 800px; overflow: hidden; }
  body {
    background: var(--backdrop);
    font-family: "Lato", Arial, sans-serif;
    position: relative;
  }
  .card {
    position: absolute;
    top: 252px;
    width: 520px;
    height: 297px;
    border-radius: 16px;
    box-shadow: 0 6px 18px rgba(0,0,0,0.18);
    overflow: hidden;
  }
  .card--front { left: 50px; background: var(--magenta); color: var(--paper); }
  .card--back  { left: 630px; background: var(--paper); }

  .brand { font-family: "Varela Round", "Lato", sans-serif; font-weight: 400; }
  .brand__mark {
    display: inline-block;
    border-radius: 50%;
    vertical-align: middle;
  }

  /* front */
  .front-brand {
    position: absolute;
    left: 0; right: 0; top: 78px;
    text-align: center;
    color: var(--paper);
  }
  .front-brand .brand__name { font-size: 56px; line-height: 1; letter-spacing: 1px; }
  .front-brand .brand__mark { width: 26px; height: 26px; background: var(--paper); margin-right: 10px; position: relative; top: -6px; }
  .front-brand .brand__sub { font-size: 27px; line-height: 1.2; letter-spacing: 2px; margin-top: 4px; }
  .front-web {
    position: absolute; left: 0; right: 0; bottom: 44px;
    text-align: center; font-size: 16px; letter-spacing: 0.5px;
  }
  .front-web .domain { color: var(--sun); }

  /* back */
  .back-brand {
    position: absolute; right: 34px; top: 34px;
    text-align: right; color: var(--sun);
  }
  .back-brand .brand__name { font-size: 40px; line-height: 1; }
  .back-brand .brand__mark { width: 18px; height: 18px; background: var(--sun); margin-right: 8px; position: relative; top: -4px; }
  .back-brand .brand__sub { font-size: 19px; letter-spacing: 1.5px; margin-top: 2px; }

  .person { position: absolute; left: 34px; top: 150px; }
  .person__name { color: var(--sun); font-size: 21px; letter-spacing: 1px; text-transform: uppercase; }
  .person__title { color: var(--ink); font-size: 15px; margin-top: 2px; }
  .rule {
    position: absolute; left: 34px; right: 70px; top: 210px;
    height: 2px; background: var(--magenta);
  }
  .contact {
    position: absolute; left: 34px; top: 220px;
    color: var(--ink); font-size: 12.5px; line-height: 1.5;
  }
</style>
</head>
<body>
  <section class="card card--front" aria-label="Business card front">
    <div class="front-brand brand">
      <div class="brand__name"><span class="brand__mark"></span>maplebrook</div>
      <div class="brand__sub">pediatric dentistry</div>
    </div>
    <p class="front-web">www.<span class="domain">maplebrookkidsdental.example</span></p>
  </section>

  <section class="card card--back" aria-label="Business card back">
    <div class="back-brand brand">
      <div class="brand__name"><span class="brand__mark"></span>maplebrook</div>
      <div class="brand__sub">pediatric dentistry</div>
    </div>
    <div class="person">
      <p class="person__name">Corinne Walbeck</p>
      <p class="person__title">DMD</p>
    </div>
    <div class="rule"></div>
    <div class="contact">
      <p>482 Quarry Lane Suite 517 Fernhollow, ST 00000</p>
      <p>Cell: 555.555.0193 | Email: info@maplebrookkidsdental.example</p>
      <p>www.maplebrookkidsdental.example</p>
    </div>
  </section>
</body>
</html>
```